Yacht, Boats, Watersports company needs a redesign of business card

Hello Designers!
We are a Boat dealership company that sells fun in the water, we sell boats, Yachts, Kayaks and also yacht WaterSport toys. We are looking to redesign our business cards in to something a little bit more sophisticated. in a way that we can make better use of our company colors. I'm attaching a zipped file containing the company 3 sets of company logo which one is an horizontal another one is a vertical and also a chromed 3d logo. Also is included two set of business cards that we use and also some designs that i think it's interesting. We use PMS 2026c Orange and PMS 7687C Blue. I would like to see at least two different options with the orange as accent and also using blue as an accent color. It's really important for the business cards to have a font option and size that is legible to most people. Our current website is wwww.coralpennant.com. Please visit if you want to have a better feeling of the Boat dealership
You can send Single sided or double side options. We are now using single sided but we may be open for a double side option if we really like the design.
Target Market(s)
Marine, boat sales, yacht sales, water toys sales/
Contact Information for Business Card
Name: Dale Whitcombe
Address: 212 North Fenwick Lane,
Seagrove Key, FL 33090
Phone: 954-731-8842
Fax: 954:731-8843
Cell: 954-382-1490
Email: dw@coralpennant.com
Website: coralpennant.com
Requirements
Must have
- the current information of the business card provided.
logo
use the PMS Colors
Nice to have
- a touch of elegance and sophistication but simple
Should not have
- should not have any typography that is hard to read, the card should be simple but yet sophisticated.

```html
<!DOCTYPE html>
<html lang="en">
<head>
<meta charset="utf-8">
<title>Coral Pennant — Business Card</title>
<link href="https://fonts.googleapis.com/css2?family=Michroma&family=Arimo:wght@400;700&display=swap" rel="stylesheet">
<style>
  :root {
    --orange: #f0652f;
    --blue: #0d4079;
    --ink: #2b2b2b;
    --rule: #b9b9b9;
    --paper: #ffffff;
    --backdrop: #2a2a2c;
  }
  * { margin: 0; padding: 0; box-sizing: border-box; }
  html, body { width: 1200px; height: 1108px; overflow: hidden; }
  body {
    background: var(--backdrop);
    display: flex;
    align-items: center;
    justify-content: center;
    gap: 70px;
    font-family: "Arimo", Arial, sans-serif;
  }
  .card {
    width: 400px;
    height: 680px;
    border-radius: 26px;
    position: relative;
    overflow: hidden;
    box-shadow: 0 18px 40px rgba(0,0,0,.45);
  }
  .card--front {
    background: var(--paper);
    display: flex;
    flex-direction: column;
    align-items: center;
    padding-top: 140px;
    text-align: center;
  }
  .brand {
    display: flex;
    flex-direction: column;
    align-items: center;
    gap: 16px;
  }
  .brand__dot {
    width: 74px; height: 74px;
    border-radius: 50%;
    border: 7px solid var(--blue);
  }
  .brand__name {
    font-family: "Michroma", sans-serif;
    font-size: 25px;
    letter-spacing: 1px;
    color: var(--blue);
    text-transform: uppercase;
    white-space: nowrap;
  }
  .holder {
    margin-top: 76px;
    font-family: "Michroma", sans-serif;
    font-size: 22px;
    font-weight: 400;
    text-transform: uppercase;
    letter-spacing: 1px;
    white-space: nowrap;
  }
  .holder__first { color: var(--blue); }
  .holder__last { color: var(--orange); }
  .rule {
    width: 130px;
    height: 1px;
    background: var(--rule);
    margin: 20px 0 18px;
  }
  .contact {
    list-style: none;
    font-size: 17px;
    line-height: 1.5;
    color: var(--ink);
  }
  .contact__label { color: var(--blue); font-weight: 700; }
  .contact__link { color: var(--blue); }
  .address {
    font-size: 18px;
    line-height: 1.4;
    color: var(--ink);
    font-style: normal;
  }
  .card--back {
    background: linear-gradient(180deg, var(--orange) 0%, #a9564f 38%, #5a4a68 62%, var(--blue) 100%);
  }
  .back__pattern {
    position: absolute; inset: 0;
    background: linear-gradient(180deg, rgba(255,255,255,.06), rgba(255,255,255,.02));
  }
  .back__brand {
    position: absolute;
    right: 44px;
    bottom: 190px;
    display: flex;
    align-items: center;
    gap: 12px;
  }
  .back__dot {
    width: 48px; height: 48px;
    border-radius: 50%;
    border: 5px solid var(--paper);
  }
  .back__name {
    font-family: "Michroma", sans-serif;
    font-size: 14px;
    color: var(--paper);
    text-transform: uppercase;
    letter-spacing: 1px;
    white-space: nowrap;
  }
</style>
</head>
<body>
  <article class="card card--front">
    <header class="brand">
      <span class="brand__dot"></span>
      <span class="brand__name">Coral Pennant</span>
    </header>
    <h1 class="holder"><span class="holder__first">Dale</span> <span class="holder__last">Whitcombe</span></h1>
    <div class="rule"></div>
    <ul class="contact">
      <li><span class="contact__label">P:</span> 954-731-8842</li>
      <li><span class="contact__label">F:</span> 954:731-8843</li>
      <li><span class="contact__label">M:</span> 954-382-1490</li>
      <li><span class="contact__label">P:</span> dw@coralpennant.com</li>
      <li>www.<span class="contact__link">coralpennant</span>.com</li>
    </ul>
    <div class="rule"></div>
    <address class="address">212 North Fenwick Lane<br>Seagrove Key, FL 33090</address>
  </article>

  <article class="card card--back">
    <div class="back__pattern" role="img" aria-label="Faint repeating brand-mark pattern over an orange-to-blue gradient"></div>
    <div class="back__brand">
      <span class="back__dot"></span>
      <span class="back__name">Coral Pennant</span>
    </div>
  </article>
</body>
</html>
```